New Bicycle shop business card

Hi!
I'm looking for a business card for my new proffesional bike mechanics shop. This shop is only for fixing broken bikes and not selling bikes.
Peferbly a modern and sleek and modern design.
Colors: black, grey, red, white
Information:
Name: Rijwielwerkplaats Vanhoutte
Shop owner: Bart Vanhoutte & Marieke Segers
Website: www.rijwielwerkplaats-vanhoutte.be
Email: info@rijwielwerkplaats-vanhoutte.be
Phone number: +32471902368
Street adres: Kerkweg 46
9940 Bellebeke
Slogan/shop information: Herstellingen van alle merken.
Logo: see files.
Target Market(s)
People who seek a mechanic to fix or upgrade their bikes.
Contact Information for Business Card
Information:
Website: info@rijwielwerkplaats-vanhoutte.be
9940 Bellebeke
Logo: see files.

```html
<!DOCTYPE html>
<html lang="nl">
<head>
<meta charset="utf-8">
<title>Rijwielwerkplaats Vanhoutte – visitekaartje</title>
<link href="https://fonts.googleapis.com/css2?family=Lato:wght@400;700;900&display=swap" rel="stylesheet">
<style>
  :root {
    --backdrop: #3b3b3b;
    --brand-red: #e12c3f;
    --brand-grey: #a9a9ab;
    --paper-white: #ffffff;
    --ink-dark: #1d1412;
  }
  * { box-sizing: border-box; margin: 0; padding: 0; }
  html, body { width: 1200px; height: 802px; overflow: hidden; }
  body {
    background: var(--backdrop);
    font-family: "Lato", Arial, sans-serif;
    position: relative;
  }
  .card {
    position: absolute;
    top: 274px;
    width: 443px;
    height: 265px;
    overflow: hidden;
  }
  /* Front */
  .card-front { left: 136px; background: var(--brand-red); color: var(--paper-white); }
  .front-panel { position: absolute; inset: 0; }
  .panel-name {
    position: absolute;
    left: 18px;
    top: 104px;
    width: 150px;
    font-weight: 700;
    font-size: 17px;
    line-height: 1.25;
    color: var(--brand-grey);
  }
  .contact-block {
    position: absolute;
    right: 27px;
    top: 38px;
    text-align: right;
  }
  .owners { font-weight: 700; font-size: 16.5px; line-height: 20px; letter-spacing: -0.2px; }
  .role { font-size: 13px; line-height: 16px; }
  .address { margin-top: 54px; font-size: 13px; line-height: 16px; }
  .lines { margin-top: 13px; font-size: 13px; line-height: 16px; }
  .line { display: flex; justify-content: flex-end; align-items: center; gap: 2px; }
  .icon { width: 10px; height: 10px; flex: none; }
  /* Back */
  .card-back {
    left: 624px;
    background: var(--ink-dark);
    color: var(--paper-white);
    display: flex;
    flex-direction: column;
    align-items: center;
    text-align: center;
  }
  .brand-mark {
    margin-top: 78px;
    width: 46px;
    height: 46px;
    background: var(--brand-red);
  }
  .brand-name {
    margin-top: 16px;
    font-weight: 700;
    font-size: 22px;
    line-height: 26px;
    color: var(--paper-white);
  }
  .slogan {
    margin-top: 14px;
    font-size: 13px;
    letter-spacing: 0.1px;
    text-transform: uppercase;
  }
</style>
</head>
<body>
  <section class="card card-front">
    <svg class="front-panel" viewBox="0 0 443 265" width="443" height="265" aria-hidden="true">
      <path d="M0 0 H200 Q190 150 120 265 H0 Z" fill="#ffffff"/>
    </svg>
    <div class="panel-name">Rijwielwerkplaats Vanhoutte</div>
    <div class="contact-block">
      <p class="owners">Bart Vanhoutte<br>Marieke Segers</p>
      <p class="role">Owner</p>
      <p class="address">Kerkweg 46<br>9940 Bellebeke</p>
      <div class="lines">
        <p class="line">+32471902368
          <svg class="icon" viewBox="0 0 10 10" aria-hidden="true"><path d="M1 3 Q5 0 9 3 L8 4.5 L6.5 3.5 H3.5 L2 4.5 Z M2.5 5 H7.5 L8.5 9 H1.5 Z" fill="#fff"/></svg></p>
        <p class="line">info@rijwielwerkplaats-vanhoutte.be
          <svg class="icon" viewBox="0 0 10 10" aria-hidden="true"><rect x="0.5" y="2" width="9" height="6.5" fill="#fff"/><path d="M0.5 2 L5 6 L9.5 2" stroke="#e12c3f" stroke-width="0.9" fill="none"/></svg></p>
        <p class="line">www.rijwielwerkplaats-vanhoutte.be
          <svg class="icon" viewBox="0 0 10 10" aria-hidden="true"><circle cx="5" cy="5" r="4.5" fill="#fff"/><path d="M2.5 3.5 Q4 2.5 5 4 Q4 6 6.5 7" stroke="#e12c3f" stroke-width="1.1" fill="none"/></svg></p>
      </div>
    </div>
  </section>

  <section class="card card-back">
    <div class="brand-mark" aria-hidden="true"></div>
    <p class="brand-name">Rijwielwerkplaats Vanhoutte</p>
    <p class="slogan">Herstellingen van alle merken</p>
  </section>
</body>
</html>
```